Venture Capital Investment Firm

We are looking to overhaul our existing website (substantially), with only using the same logos (which we can provide).
We are an investment firm that focuses on making loans to late stage technology companies. Our site should ultimately look like other venture capital firms, and look modern and fresh. We have an existing website www.norvellhub.com which this will be replacing, although we will be using a lot of the existing written content, and potentially the numbers of pages we will need, we are not wed to anything else. Please feel free to shoot any questions at any time and thank you in advance for your help!
Websites we like as examples:
https://www.tesmarkfund.com/
https://www.brindlewoodpartners.com/
Target Market(s)
Potential investors who will invest in our firm, as well as potentially companies that are looking to borrow money from us.
Coding
Coded - Design and coding required
Number of Pages Required
5+ page
Colors
Designer to choose colors to be used in the design.
Look and feel

```html
<!DOCTYPE html>
<html lang="en">
<head>
<meta charset="utf-8">
<title>Norvell Hub — Recent News</title>
<link href="https://fonts.googleapis.com/css2?family=Raleway:wght@300;400;500&display=swap" rel="stylesheet">
<style>
:root{
  --navy:#0d1a4a;
  --ink:#1b2550;
  --teal:#6a9fb5;
  --teal-line:#2a7fa5;
  --tag-bg:#f3f5f6;
  --sand:#d4a27a;
  --grey:#8a8f99;
  --foot:#0f3a4c;
  --white:#ffffff;
}
*{box-sizing:border-box;margin:0;padding:0}
html,body{width:880px;height:1200px;overflow:hidden;background:var(--white)}
body{font-family:"Raleway",sans-serif;color:var(--ink);position:relative}
.hero{position:absolute;left:0;top:0;width:880px;height:401px;
  background:linear-gradient(180deg,#5d98b3 0%,#a9c7d9 35%,#dfe6ee 58%,#ead9d6 72%,#b79a8a 82%,#5a5e66 92%,#3b3f47 100%)}
.topbar{position:absolute;top:14px;left:110px;right:110px;height:34px;display:flex;align-items:center}
.brand{display:flex;align-items:center;gap:8px;width:150px}
.brand-dot{width:16px;height:16px;border-radius:50%;background:var(--navy)}
.brand-name{font-weight:500;font-size:15px;color:var(--navy);letter-spacing:.5px}
.nav{display:flex;gap:41px;margin-left:32px;font-size:8px;letter-spacing:.4px;color:var(--ink)}
.nav .current{text-decoration:underline}
.login{margin-left:auto;border:1px solid var(--ink);border-radius:16px;padding:9px 16px;font-size:8px;letter-spacing:.4px}
.hero-title{position:absolute;top:154px;width:100%;text-align:center;font-weight:400;font-size:33px;color:var(--navy)}
.hero-sub{position:absolute;top:201px;width:100%;text-align:center;font-weight:300;font-size:12px}
.divider{position:absolute;left:440px;top:370px;width:1px;height:62px;background:var(--teal-line)}
.news{position:absolute;top:486px;left:110px;width:670px;list-style:none}
.news li{display:flex;align-items:center;height:35.2px}
.tag{font-size:10px;letter-spacing:.3px;background:var(--tag-bg);padding:2px 6px;color:var(--teal)}
.tag.portfolio{color:var(--sand)}
.tag-cell{width:132px}
.headline{flex:1;font-size:11px;font-weight:500;color:var(--navy)}
.date{width:70px;text-align:center;font-size:9.5px;color:var(--grey);letter-spacing:.3px}
.cta{position:absolute;top:778px;left:392px;width:96px;height:32px;border:1px solid var(--navy);border-radius:16px;
  display:flex;align-items:center;justify-content:center;font-size:10px;color:var(--navy)}
.footer{position:absolute;top:948px;left:0;width:880px;height:252px;
  background:linear-gradient(180deg,#0e3b4e 0%,#1d4656 55%,#2a4d5c 75%,#1c3a48 100%);color:var(--white)}
.foot-brand{position:absolute;top:70px;width:100%;display:flex;justify-content:center;align-items:center;gap:12px}
.foot-dot{width:26px;height:26px;border-radius:50%;background:var(--white)}
.foot-name{font-size:32px;font-weight:400;letter-spacing:.5px}
.foot-nav{position:absolute;top:150px;width:100%;display:flex;justify-content:center;gap:44px;font-size:8px;letter-spacing:.4px}
.foot-legal{position:absolute;top:226px;width:100%;text-align:center;font-size:5px;line-height:8.5px}
.foot-legal u{text-decoration:underline}
</style>
</head>
<body>
<header class="hero" role="img" aria-label="Aerial photograph of a city skyline at dawn under a pale blue sky">
  <div class="topbar">
    <div class="brand"><span class="brand-dot"></span><span class="brand-name">Norvell Hub</span></div>
    <nav class="nav"><span>STRATEGY</span><span>ABOUT US</span><span>TEAM</span><span class="current">NEWS</span><span>CONTACT</span></nav>
    <span class="login">INVESTORS LOGIN</span>
  </div>
  <h1 class="hero-title">Recent News</h1>
  <p class="hero-sub">Our recent press release &amp; portfolio news</p>
</header>
<div class="divider"></div>
<ul class="news">
  <li><span class="tag-cell"><span class="tag">PRESS RELEASE</span></span><span class="headline">Norvell Hub completes structured debt investment in Brightlane</span><span class="date">APRIL, 2018</span></li>
  <li><span class="tag-cell"><span class="tag">PRESS RELEASE</span></span><span class="headline">Norvell Hub completes $22,000,000 structured debt investment in Pollwise</span><span class="date">OCT, 2016</span></li>
  <li><span class="tag-cell"><span class="tag portfolio">PORTFOLIO NEWS</span></span><span class="headline">Corvane Semiconductor acquired by Hexaline for $55,000,000</span><span class="date">APRIL, 2016</span></li>
  <li><span class="tag-cell"><span class="tag">PRESS RELEASE</span></span><span class="headline">Norvell Hub closes inaugural $100,000,000 investment vehicle</span><span class="date">JULY, 2015</span></li>
  <li><span class="tag-cell"><span class="tag">PRESS RELEASE</span></span><span class="headline">Completion of $36,250,000 structured credit investment in Corvane Semiconductor</span><span class="date">DEC, 2014</span></li>
  <li><span class="tag-cell"><span class="tag portfolio">PORTFOLIO NEWS</span></span><span class="headline">Quartzon acquired by Tessmoor Devices for $200,000,000</span><span class="date">OCT, 2014</span></li>
  <li><span class="tag-cell"><span class="tag">PRESS RELEASE</span></span><span class="headline">Norvell Hub completes $15,000,000 structured credit investment in Quartzon</span><span class="date">SEPT, 2014</span></li>
</ul>
<a class="cta">Contact Us</a>
<footer class="footer" role="img" aria-label="Dusk photograph of a suspension bridge over a bay, tinted deep teal">
  <div class="foot-brand"><span class="foot-dot"></span><span class="foot-name">Norvell</span></div>
  <nav class="foot-nav"><span>STRATEGY</span><span>ABOUT US</span><span>TEAM</span><span>NEWS</span><span>CONTACT</span></nav>
  <p class="foot-legal">Norvell Hub &nbsp;•&nbsp; San Francisco<br>© 2020 Norvell Hub Investment Partners LLC. All Rights Reserved. &nbsp;| &nbsp;<u>Legal Disclaimer</u></p>
</footer>
</body>
</html>
```